Full Page Color Ad

We need a full page 8.5 x 11 ad created for a magazine. Please see the attached examples. It would be best if the wording/style stayed the same. As far as background image, we are looking for something catchy that portrays "hidden treasure". Please be sure to include the logos as well. If you have any questions or need anything else, please email mhorvent@tarquill.com You can also visit www.tarquill.com to learn at little about our company and see our branding/style.
*Please follow the style and wording of the examples as best as possible. Not looking for variation on the text layout- more ofthe background and added creativity.*
Industry/Entity Type
It Company
Look and feel

```html
<!DOCTYPE html>
<html lang="en">
<head>
<meta charset="UTF-8">
<title>Discover Hidden Value – Tarquill</title>
<link rel="stylesheet" href="https://fonts.googleapis.com/css2?family=Arimo:wght@400;700&display=swap">
<style>
  :root {
    --navy: #0f2a47;
    --gold: #f0b31a;
    --brand-blue: #0f4d94;
    --badge-blue: #2f78c4;
    --white: #ffffff;
    --sand-light: #d8c1a2;
    --sand-mid: #b39473;
    --sand-dark: #86694b;
    --key-glow: rgba(236, 196, 146, 0.85);
  }
  html, body {
    margin: 0;
    padding: 0;
    width: 900px;
    height: 1200px;
    overflow: hidden;
    background: var(--white);
  }
  .ad {
    position: relative;
    width: 900px;
    height: 1200px;
    font-family: "Arimo", Arial, sans-serif;
    color: var(--navy);
    overflow: hidden;
  }
  .top-band {
    position: absolute; left: 0; top: 0;
    width: 900px; height: 42px;
    background: var(--navy);
  }
  .headline-band {
    position: absolute; left: 0; top: 42px;
    width: 900px; height: 108px;
    background: var(--gold);
  }
  .headline {
    position: absolute; left: 74px; top: 54px;
    margin: 0;
    font-size: 75px;
    font-weight: 400;
    line-height: 1;
    letter-spacing: -0.5px;
    color: var(--navy);
    white-space: nowrap;
  }
  .headline strong { font-weight: 700; }
  .hero-photo {
    position: absolute; left: 0; top: 150px;
    width: 900px; height: 845px;
    background:
      radial-gradient(ellipse 30% 13% at 50% 70%, var(--key-glow), transparent 75%),
      radial-gradient(ellipse 18% 14% at 68% 80%, rgba(240, 205, 160, 0.6), transparent 75%),
      radial-gradient(ellipse 55% 22% at 30% 92%, rgba(110, 84, 58, 0.45), transparent 75%),
      radial-gradient(ellipse 50% 18% at 75% 45%, rgba(120, 92, 64, 0.35), transparent 75%),
      radial-gradient(ellipse 70% 30% at 65% 15%, rgba(246, 228, 204, 0.45), transparent 70%),
      radial-gradient(ellipse 45% 20% at 20% 55%, rgba(232, 210, 180, 0.4), transparent 70%),
      linear-gradient(160deg, var(--sand-light) 0%, var(--sand-mid) 50%, var(--sand-dark) 100%);
  }
  .lead-in {
    position: absolute; left: 79px; top: 168px;
    margin: 0;
    font-size: 50px;
    font-weight: 700;
    line-height: 62px;
    color: var(--navy);
  }
  .process-list {
    position: absolute; left: 244px; top: 178px;
    margin: 0; padding: 0;
    list-style: none;
    font-size: 27px;
    line-height: 34px;
    color: var(--navy);
    white-space: nowrap;
  }
  .process-list .bold { font-weight: 700; }
  .process-list .light { font-weight: 400; }
  .closing-word {
    position: absolute; left: 588px; top: 314px;
    margin: 0;
    font-size: 66px;
    line-height: 1;
    font-weight: 700;
    color: var(--navy);
    white-space: nowrap;
  }
  .footer-band {
    position: absolute; left: 0; top: 995px;
    width: 900px; height: 160px;
    background: var(--gold);
  }
  .brand-block {
    position: absolute; left: 18px; top: 1015px;
    width: 112px; height: 116px;
    background: var(--brand-blue);
  }
  .brand-name {
    position: absolute; left: 8px; top: 8px;
    font-size: 19px;
    font-weight: 700;
    color: var(--white);
  }
  .company-blurb {
    position: absolute; left: 152px; top: 1030px;
    width: 508px;
    margin: 0;
    font-size: 12px;
    line-height: 15.5px;
    color: var(--navy);
  }
  .partner-badge {
    position: absolute; left: 682px; top: 1018px;
    width: 182px; height: 112px;
  }
  .bottom-band {
    position: absolute; left: 0; top: 1155px;
    width: 900px; height: 45px;
    background: var(--navy);
  }
  .web-address {
    position: absolute; left: 18px; top: 1165px;
    margin: 0;
    font-size: 21px;
    color: var(--white);
  }
</style>
</head>
<body>
  <main class="ad">
    <div class="top-band"></div>
    <div class="headline-band"></div>
    <h1 class="headline">Discover <strong>Hidden</strong> Value</h1>

    <div class="hero-photo" role="img" aria-label="Photograph of an old golden key half buried in rippled sand, lying in the lower middle of the page"></div>

    <p class="lead-in">From<br>Your</p>
    <ul class="process-list">
      <li class="bold">CONSOLIDATIONS</li>
      <li class="light">FINANCIAL PLANNING</li>
      <li class="bold">STRATEGY MANAGEMENT</li>
      <li class="light">PROFITABILITY</li>
      <li class="bold">PERFORMANCE</li>
      <li class="bold">MANAGEMENT</li>
      <li class="light">BALANCED SCORECARD</li>
      <li class="bold">SALES &amp; OPERATIONS</li>
      <li class="light">PLANNING</li>
    </ul>
    <p class="closing-word">Process.</p>

    <div class="footer-band"></div>
    <div class="brand-block"><span class="brand-name">tarquill</span></div>
    <p class="company-blurb">Tarquill is trusted by more companies globally to deliver high value solutions featuring Veltrix's Business Analytics portfolio. Our team offers visionary services that maximize the business value your company can realize from these powerful products. Contact us today for more information.</p>
    <svg class="partner-badge" viewBox="0 0 182 112" aria-label="Partner badge">
      <rect x="0" y="0" width="182" height="112" fill="var(--badge-blue)"/>
    </svg>

    <div class="bottom-band"></div>
    <p class="web-address">www.tarquill.com</p>
  </main>
</body>
</html>
```